Business Name: DM Space Arranging Pty Ltd

Business Type: Professional Home Styling and Minor Renovation Business

Logo: Attached is the logo that has been created.
I always envisaged the logo in the middle of the business card with my full name underneath it.

Marnie Tulloch B.Com LMR HTV
Property Stylist & Project Manager

Include dot points of services
Staging Houses for Sale
Minor Home Renovations
Home Styling & Project Management
Re-Designing Living Spaces to Aid the Disabled

Somewhere on the card I would like to incorporate
"Property Styling and Cosmetic Renovations"

Colour Scheme:
Gloss black business card, with white and then
Gold or Silver as the highlight colours.

Incorporate a small amount of yellow only if possible to make it pop. If this really doesn’t work it doesn’t have to be used. Also l like the colour teal if that needs to be used as a contrast colour.

Feel/Themes
• I love antique chairs, regal expensive looking furniture mixed with modern homes (this is the unique style I want to sell) antique and modern mix that looks high class as well as modern and fresh, targeting an executive market.
• I want to use an orchid as a trademark throughout the course of my work, not sure if this can somehow be incorporated? Also really like crowns to give that regal/antique feel and then something else to give that modern twist (I don’t know what the something else could be)
• Wall Paper Look (on a portion of it not all of it, like a French look)
• Overall feel - A very deluxe and professional feel with a little bit of creative flare.

I hope this helps create a bit of a picture.

Is it ok that I call you tomorrow morning? My mobile number is 0438 926 574 if you have any questions for me in the meantime.

Target Market(s)

High Quality Executive Market - People selling homes

Industry/Entity Type

Business

Contact Information for Business Card

Include dot points of services:
Staging Houses for Sale
Minor Home Renovations

Font styles to use
Serif
Script

Colors
33b8a4
fbed22

Requirements
Must have
• Marnie Tulloch B.Com LMR HTV
• Property Stylist & Project Manager
• LMR and HTV Logos on the card
• "Dramatically increase the value of your property"
Nice to have
• Colour Scheme:
• Gloss black business card, with white and then
• Gold or Silver as the highlight colours.
• Incorporate a small amount of yellow only if possible to make it pop. If this really doesn’t work it doesn’t have to be used. Also l like the colour teal if that needs to be used as a contrast colour.
• Also like teal as a highlight colour.

```html
<!DOCTYPE html>
<html lang="en">
<head>
<meta charset="utf-8">
<title>DM Space Arranging Pty Ltd – Business Cards</title>
<link rel="stylesheet" href="https://fonts.googleapis.com/css2?family=Arimo:wght@400&family=Pinyon+Script&family=Tinos:ital,wght@0,400;1,400&display=swap">
<style>
  :root {
    --backdrop: #1e1e20;
    --card-white: #ffffff;
    --gloss-black: #0b0b0c;
    --silver: #9a9a9a;
    --silver-light: #b9b9b9;
    --gold: #c9a13b;
    --yellow: #f2c21b;
    --ink: #111111;
  }
  * { margin: 0; padding: 0; box-sizing: border-box; }
  html, body {
    width: 1200px;
    height: 852px;
    overflow: hidden;
    background: var(--backdrop);
  }
  .stage {
    position: relative;
    width: 1200px;
    height: 852px;
  }
  .card {
    position: absolute;
    width: 520px;
    height: 300px;
    border-radius: 12px;
    overflow: hidden;
    background: var(--card-white);
    box-shadow: 0 14px 30px rgba(0,0,0,.55);
  }
  .card--front { left: 50px; top: 190px; }
  .card--back  { left: 630px; top: 362px; }

  .brand-name {
    position: absolute;
    left: 0; right: 0;
    text-align: center;
    font-family: "Tinos", serif;
    font-size: 15px;
    letter-spacing: 4px;
    text-transform: uppercase;
    color: var(--ink);
  }
  .card--front .brand-name { top: 112px; }
  .card--back  .brand-name { top: 70px; }

  .gloss-band {
    position: absolute;
    left: 0; right: 0; bottom: 0;
    background: linear-gradient(180deg, #1a1a1c 0%, var(--gloss-black) 45%, #000 100%);
  }
  .card--front .gloss-band { height: 120px; }
  .card--back  .gloss-band { height: 54px; }

  .holder {
    position: absolute;
    left: 0; right: 0;
    top: 196px;
    text-align: center;
  }
  .holder__name {
    font-family: "Pinyon Script", cursive;
    font-size: 34px;
    line-height: 1;
    color: var(--gold);
  }
  .holder__credentials,
  .holder__role {
    font-family: "Tinos", serif;
    font-size: 14px;
    color: var(--silver);
    line-height: 1.3;
  }
  .holder__credentials { margin-top: 4px; }

  .services {
    position: absolute;
    left: 54px;
    top: 130px;
    list-style: none;
    font-family: "Arimo", sans-serif;
    font-size: 17px;
    color: var(--ink);
    line-height: 1.45;
  }
  .services__row { display: flex; gap: 18px; }
  .services__item::before {
    content: "»";
    color: var(--yellow);
    margin-right: 8px;
  }
  .services__row--indent-1 { padding-left: 24px; }
  .services__row--indent-2 { padding-left: 0; }

  .tagline {
    position: absolute;
    left: 0; right: 0;
    bottom: 16px;
    text-align: center;
    font-family: "Tinos", serif;
    font-style: italic;
    font-size: 18px;
    letter-spacing: .5px;
    color: var(--silver-light);
  }
</style>
</head>
<body>
<main class="stage">

  <section class="card card--front" aria-label="Business card front">
    <p class="brand-name">DM Space Arranging Pty Ltd</p>
    <div class="gloss-band"></div>
    <div class="holder">
      <p class="holder__name">Marnie Tulloch</p>
      <p class="holder__credentials">B.Com LMR HTV</p>
      <p class="holder__role">Property Stylist &amp; Project Manager</p>
    </div>
  </section>

  <section class="card card--back" aria-label="Business card back">
    <p class="brand-name">DM Space Arranging Pty Ltd</p>
    <ul class="services">
      <li class="services__row">
        <span class="services__item">Staging Houses for Sale</span>
        <span class="services__item">Minor Home Renovations</span>
      </li>
      <li class="services__row services__row--indent-1">
        <span class="services__item">Home Styling &amp; Project Management</span>
      </li>
      <li class="services__row services__row--indent-2">
        <span class="services__item">Re-Designing Living Spaces to Aid the Disabled</span>
      </li>
    </ul>
    <div class="gloss-band"></div>
    <p class="tagline">Property Styling &amp; Cosmetic Renovations</p>
  </section>

</main>
</body>
</html>
```